Meridale Bed Company Needs Business Card

Looking for a very nice looking business card. Creative but not extravagant. We sell beds and pillows across the U.S. and need something professional but catchy. I have attached the logo.

Name : Devin Holt
Title : President
Phone : (800) 471-2960
Email: sleep@quilmora.com
Website: www.quilmora.com

Can be single-sided or double-sided
horizontal or vertical

Can use Blues/Greys

Target Market(s)

Mass Market

Industry/Entity Type

Retail

Contact Information for Business Card

Name : Devin Holt
Title : President
Phone : (800) 471-2960
Email: sleep@quilmora.com
Website: www.quilmora.com

Requirements
Must have
• Clean, Modern, Smooth
• Can use Blues/Greys
• On the other side without the information - have something simple like www.quilmora.com or our logo
Nice to have
• Surprise me
Should not have
• Nothing crazy, nothing cluttered

```html
<!DOCTYPE html>
<html lang="en">
<head>
<meta charset="utf-8">
<title>Meridale Bed Company – Business Card</title>
<link href="https://fonts.googleapis.com/css2?family=Open+Sans:wght@300;400;600&display=swap" rel="stylesheet">
<style>
  :root {
    --stage: #161616;
    --brand-blue: #35a6da;
    --card-white: #ffffff;
    --ink: #2b2b2b;
  }
  html, body {
    margin: 0;
    padding: 0;
    width: 1200px;
    height: 900px;
    overflow: hidden;
    background: var(--stage);
    font-family: "Open Sans", Arial, sans-serif;
  }
  .canvas {
    position: relative;
    width: 1200px;
    height: 900px;
  }
  .card {
    position: absolute;
    top: 170px;
    width: 347px;
    height: 561px;
    overflow: hidden;
  }
  .card--front {
    left: 259px;
    background: var(--card-white);
  }
  .card--back {
    left: 631px;
    background: var(--brand-blue);
  }
  .tab {
    position: absolute;
    left: 102px;
    width: 143px;
    height: 30px;
    background: var(--brand-blue);
  }
  .tab--top { top: 0; }
  .tab--bottom { bottom: 0; height: 28px; }
  .wordmark {
    position: absolute;
    left: 0;
    width: 100%;
    text-align: center;
    font-weight: 300;
    line-height: 1;
    letter-spacing: 1px;
  }
  .card--front .wordmark {
    top: 125px;
    font-size: 58px;
    color: var(--brand-blue);
  }
  .card--back .wordmark {
    top: 262px;
    font-size: 64px;
    color: var(--card-white);
  }
  .contact {
    position: absolute;
    top: 294px;
    left: 0;
    width: 100%;
    text-align: center;
    color: var(--ink);
  }
  .contact__name {
    margin: 0;
    font-size: 22px;
    font-weight: 600;
    color: var(--brand-blue);
    line-height: 30px;
  }
  .contact__title {
    margin: 0;
    font-size: 15px;
    line-height: 20px;
  }
  .contact__lines {
    margin: 26px 0 0;
    font-size: 15px;
    line-height: 20px;
  }
  .contact__web {
    margin: 28px 0 0;
    font-size: 15px;
    font-weight: 600;
  }
  .back-web {
    position: absolute;
    top: 416px;
    left: 0;
    width: 100%;
    text-align: center;
    font-size: 16px;
    font-weight: 600;
    color: var(--card-white);
  }
</style>
</head>
<body>
<main class="canvas">
  <section class="card card--front" aria-label="Business card front">
    <div class="tab tab--top"></div>
    <div class="wordmark">quilmora</div>
    <div class="contact">
      <p class="contact__name">Devin Holt</p>
      <p class="contact__title">President</p>
      <p class="contact__lines">(800) 471-2960<br>sleep@quilmora.com</p>
      <p class="contact__web">www.quilmora.com</p>
    </div>
    <div class="tab tab--bottom"></div>
  </section>

  <section class="card card--back" aria-label="Business card back">
    <div class="wordmark">quilmora</div>
    <div class="back-web">www.quilmora.com</div>
  </section>
</main>
</body>
</html>
```